Copperleaf Roofing Business Card

This is my current business card. But I’d like to make some changes. Somewhere on the card I’d like to list some of the services we offer. Maybe on the back? But I’d still like to keep the red. White and black modern look.

-residential & commercial roofing
-Roof Repairs & Maintenance
-Storm Damage & Insurance Claims specialist
-Christmas Lights and permanent Christmas lights
Fencing. Windows. Gutters. Siding. Sheetrock, painting.

```html
<!DOCTYPE html>
<html lang="en">
<head>
<meta charset="UTF-8">
<title>Copperleaf Roofing Business Card</title>
<link rel="stylesheet" href="https://fonts.googleapis.com/css2?family=Poppins:wght@300;400;600;700&family=Michroma&display=swap">
<style>
  :root {
    --page: #e2e6e7;
    --card: #171717;
    --red: #e52421;
    --white: #ffffff;
    --faint: #1f1f1f;
    --faint-edge: #2a2a2a;
  }
  * { margin: 0; padding: 0; box-sizing: border-box; }
  html, body { width: 1200px; height: 960px; overflow: hidden; }
  body {
    background: var(--page);
    font-family: 'Poppins', sans-serif;
    position: relative;
  }
  .card {
    position: absolute;
    left: 252px;
    width: 700px;
    height: 398px;
    background: var(--card);
    border-radius: 28px;
    box-shadow: -4px 4px 0 var(--red), -6px 14px 22px rgba(0,0,0,0.28);
    color: var(--white);
  }
  .card--back { top: 60px; }
  .card--front { top: 500px; }

  /* Back side */
  .emboss-mark {
    position: absolute;
    left: 296px; top: 30px;
    width: 108px; height: 108px;
    border-radius: 50%;
    background: var(--faint);
    box-shadow: inset 0 0 0 1px var(--faint-edge);
  }
  .emboss-name {
    position: absolute;
    left: 0; right: 0; top: 146px;
    text-align: center;
    font-weight: 700;
    color: var(--faint-edge);
    line-height: 1.05;
  }
  .emboss-name .line1 { display: block; font-size: 28px; letter-spacing: 1px; }
  .emboss-name .line2 { display: block; font-size: 18px; letter-spacing: 2px; }
  .services {
    position: absolute;
    left: 0; right: 0; top: 237px;
    text-align: center;
  }
  .services h2 {
    color: var(--red);
    font-weight: 600;
    font-size: 19px;
    letter-spacing: 0.3px;
    line-height: 26px;
  }
  .services ul { list-style: none; }
  .services li {
    font-weight: 300;
    font-size: 16px;
    line-height: 22.8px;
    letter-spacing: 0.4px;
  }

  /* Front side */
  .brand-mark {
    position: absolute;
    left: 91px; top: 107px;
    width: 122px; height: 122px;
    border-radius: 50%;
    background: var(--red);
  }
  .brand-name {
    position: absolute;
    left: 20px; width: 264px; top: 242px;
    text-align: center;
    font-weight: 700;
    color: var(--white);
    line-height: 1.1;
  }
  .brand-name .line1 { display: block; font-size: 27px; letter-spacing: 1px; }
  .brand-name .line2 { display: block; font-size: 19px; letter-spacing: 2px; }
  .divider {
    position: absolute;
    left: 350px; top: 95px;
    width: 1px; height: 212px;
    background: var(--red);
    opacity: 0.7;
  }
  .person {
    position: absolute;
    left: 395px; top: 120px;
  }
  .person-name {
    font-family: 'Michroma', sans-serif;
    font-size: 25px;
    line-height: 36px;
    letter-spacing: 0.5px;
    white-space: nowrap;
  }
  .person-name .first { color: var(--red); }
  .person-role {
    font-weight: 600;
    font-size: 16px;
    letter-spacing: 0.5px;
    margin-top: 2px;
  }
  .contacts {
    position: absolute;
    left: 395px; top: 211px;
    list-style: none;
  }
  .contacts li {
    display: flex;
    align-items: center;
    height: 22.5px;
    font-size: 17.5px;
    letter-spacing: 0.4px;
    white-space: nowrap;
  }
  .contacts svg { width: 17px; height: 17px; margin-right: 11px; flex: none; }
</style>
</head>
<body>

<section class="card card--back">
  <div class="emboss-mark"></div>
  <div class="emboss-name"><span class="line1">COPPERLEAF</span><span class="line2">ROOFING CO.</span></div>
  <div class="services">
    <h2>SERVICES WE OFFER</h2>
    <ul>
      <li>Roof Repairs &amp; Maintenance</li>
      <li>Residential &amp; Commercial Roofing</li>
      <li>Storm Damage &amp; Insurance Claims Specialist</li>
      <li>Christmas Lights and Permanent Christmas lights</li>
      <li>Fencing. Windows. Gutters. Siding. Sheetrock, Painting</li>
    </ul>
  </div>
</section>

<section class="card card--front">
  <div class="brand-mark"></div>
  <div class="brand-name"><span class="line1">COPPERLEAF</span><span class="line2">ROOFING CO.</span></div>
  <div class="divider"></div>
  <div class="person">
    <div class="person-name"><span class="first">DYLAN</span> MARSH</div>
    <div class="person-role">OWNER</div>
  </div>
  <ul class="contacts">
    <li>
      <svg viewBox="0 0 24 24" aria-hidden="true"><path fill="#e52421" d="M6.6 10.8a15.1 15.1 0 0 0 6.6 6.6l2.2-2.2a1 1 0 0 1 1-.25 11.4 11.4 0 0 0 3.6.57 1 1 0 0 1 1 1V20a1 1 0 0 1-1 1A17 17 0 0 1 3 4a1 1 0 0 1 1-1h3.5a1 1 0 0 1 1 1c0 1.25.2 2.45.57 3.57a1 1 0 0 1-.25 1z"/></svg>
      682-555-0148
    </li>
    <li>
      <svg viewBox="0 0 24 24" aria-hidden="true"><circle cx="12" cy="12" r="10" fill="#e52421"/><path d="M2 12h20M12 2c3 3 3 17 0 20M12 2c-3 3-3 17 0 20" stroke="#171717" stroke-width="1.3" fill="none"/></svg>
      www.copperleafroofing.co
    </li>
    <li>
      <svg viewBox="0 0 24 24" aria-hidden="true"><rect x="2" y="6" width="20" height="14" rx="1.5" fill="#e52421"/><path d="M2 7l10 7 10-7" stroke="#171717" stroke-width="1.5" fill="none"/></svg>
      dylan@copperleafroofing.co
    </li>
  </ul>
</section>

</body>
</html>
```